Corvin Ridge Software PowerPoint template

We are a software company selling endpoint visibility, access and security technology to enterprise-level IT departments.
Our technology helps organizations gain comprehensive visibility into and control over devices accessing their corporate network so they can quickly identify and address suspicious activity on the network that could lead to potential threats like data breaches.
This technology can cost organizations upwards of $1M - depending on the size of the organization. Our primary clients are Vestral 2,000 companies.
We want a professional, polished PowerPoint template that we can use for all company presentations. Please include:
Title page
Section page
General info page
Thank you page
Logo options and color specs are attached.
Please include our tagline on at least the title page: Discover the edge. Optimize the whole.
Reason: Seeking more options. Looking for a clean design that uses lots of white space.
Software

```html
<!DOCTYPE html>
<html lang="en">
<head>
<meta charset="utf-8">
<title>Meet our Team – Corvin Ridge Software</title>
<link href="https://fonts.googleapis.com/css2?family=Oxygen:wght@400;700&family=Carlito&display=swap" rel="stylesheet">
<style>
  :root {
    --maroon: #8c1d1d;
    --copper: #d4825e;
    --ink: #1a1a1a;
    --grey: #555555;
    --rule: #b8b8b8;
    --pattern-tone: #f1f1f1;
    --paper: #ffffff;
    --photo-light: #d9d9d9;
    --photo-dark: #6b6b6b;
  }
  * { margin: 0; padding: 0; box-sizing: border-box; }
  html, body { width: 1200px; height: 849px; overflow: hidden; background: var(--paper); }
  .slide {
    position: relative;
    width: 1200px;
    height: 849px;
    background: var(--paper);
    font-family: "Oxygen", sans-serif;
    color: var(--ink);
    overflow: hidden;
  }
  .accent-bar {
    position: absolute; left: 134px; top: 0;
    width: 6px; height: 86px;
    background: var(--maroon);
  }
  .slide-header { position: absolute; left: 163px; top: 36px; }
  .slide-header__title {
    font-size: 20px; color: var(--maroon); letter-spacing: 0.2px; line-height: 24px;
  }
  .slide-header__date {
    font-size: 19px; color: var(--ink); line-height: 26px;
  }
  .slide-header__date strong { font-weight: 700; }
  .pattern-area {
    position: absolute; left: 820px; top: 0;
    width: 380px; height: 360px;
    background: radial-gradient(ellipse at 75% 30%, var(--pattern-tone) 0%, var(--paper) 70%);
  }
  .page-number {
    position: absolute; left: 1099px; top: 36px;
    width: 56px; height: 56px; border-radius: 50%;
    background: var(--copper); color: var(--paper);
    font-size: 17px; font-weight: 700;
    display: flex; align-items: center; justify-content: center;
  }
  .slide-title {
    position: absolute; left: 128px; top: 170px;
    font-size: 66px; font-weight: 700; color: var(--copper);
    line-height: 80px; letter-spacing: -0.5px;
  }
  .team { position: absolute; left: 0; top: 0; width: 100%; }
  .member {
    position: absolute; top: 279px; width: 240px;
    text-align: center;
  }
  .member__portrait { display: block; margin: 0 auto; }
  .member__name {
    margin-top: 8px;
    font-size: 30px; color: var(--maroon); line-height: 36px; font-weight: 400;
  }
  .member__role {
    font-size: 21px; color: var(--ink); line-height: 26px;
  }
  .member__bio {
    margin-top: 12px;
    font-family: "Carlito", sans-serif;
    font-size: 16.5px; line-height: 24.3px; color: var(--ink);
  }
  .footer-rule {
    position: absolute; left: 130px; top: 770px;
    width: 706px; height: 1px; background: var(--rule);
  }
  .footer-copy {
    position: absolute; left: 130px; top: 778px;
    font-size: 12.5px; color: var(--grey);
  }
  .brand {
    position: absolute; left: 860px; top: 748px;
    display: flex; align-items: center; gap: 16px;
  }
  .brand__mark {
    flex: none;
    width: 40px; height: 40px; border-radius: 50%; background: var(--copper);
  }
  .brand__name {
    font-size: 22px; font-weight: 700; color: var(--maroon);
    letter-spacing: 1.5px; line-height: 26px; text-transform: uppercase;
    white-space: nowrap;
  }
</style>
</head>
<body>
<main class="slide">
  <div class="accent-bar"></div>
  <header class="slide-header">
    <p class="slide-header__title">PPT HEADING GOES HERE</p>
    <p class="slide-header__date">FEB, <strong>2015</strong></p>
  </header>

  <div class="pattern-area" role="img" aria-label="Decorative pattern of outlined circles"></div>
  <div class="page-number">01</div>

  <h1 class="slide-title">Meet our Team</h1>

  <svg width="0" height="0" aria-hidden="true" style="position:absolute">
    <defs>
      <radialGradient id="photoTone" cx="50%" cy="40%" r="60%">
        <stop offset="0%" stop-color="#d9d9d9"/>
        <stop offset="100%" stop-color="#6b6b6b"/>
      </radialGradient>
    </defs>
  </svg>

  <section class="team">
    <article class="member" style="left:93px">
      <svg class="member__portrait" width="200" height="200" viewBox="0 0 200 200">
        <circle cx="100" cy="100" r="97" fill="none" stroke="var(--copper)" stroke-width="1.5"/>
        <circle cx="100" cy="100" r="81" fill="url(#photoTone)" role="img" aria-label="Portrait photo of team member"/>
      </svg>
      <h2 class="member__name">JOHN DOE</h2>
      <p class="member__role">Manager</p>
      <p class="member__bio">corporate network<br>so they can quickly<br>identify and address<br>suspicious activity<br>on the network<br>that could lead to</p>
    </article>

    <article class="member" style="left:328px">
      <svg class="member__portrait" width="200" height="200" viewBox="0 0 200 200">
        <circle cx="100" cy="100" r="97" fill="none" stroke="var(--copper)" stroke-width="1.5"/>
        <circle cx="100" cy="100" r="81" fill="url(#photoTone)" role="img" aria-label="Portrait photo of team member"/>
      </svg>
      <h2 class="member__name">JOHN DOE</h2>
      <p class="member__role">Manager</p>
      <p class="member__bio">corporate network<br>so they can quickly<br>identify and address<br>suspicious activity<br>on the network<br>that could lead to</p>
    </article>

    <article class="member" style="left:562px">
      <svg class="member__portrait" width="200" height="200" viewBox="0 0 200 200">
        <circle cx="100" cy="100" r="97" fill="none" stroke="var(--copper)" stroke-width="1.5"/>
        <circle cx="100" cy="100" r="81" fill="url(#photoTone)" role="img" aria-label="Portrait photo of team member"/>
      </svg>
      <h2 class="member__name">JOHN DOE</h2>
      <p class="member__role">Manager</p>
      <p class="member__bio">corporate network<br>so they can quickly<br>identify and address<br>suspicious activity<br>on the network<br>that could lead to</p>
    </article>

    <article class="member" style="left:795px">
      <svg class="member__portrait" width="200" height="200" viewBox="0 0 200 200">
        <circle cx="100" cy="100" r="97" fill="none" stroke="var(--copper)" stroke-width="1.5"/>
        <circle cx="100" cy="100" r="81" fill="url(#photoTone)" role="img" aria-label="Portrait photo of team member"/>
      </svg>
      <h2 class="member__name">JOHN DOE</h2>
      <p class="member__role">Manager</p>
      <p class="member__bio">corporate network<br>so they can quickly<br>identify and address<br>suspicious activity<br>on the network<br>that could lead to</p>
    </article>
  </section>

  <div class="footer-rule"></div>
  <p class="footer-copy">©2015 Corvin Ridge Software</p>

  <div class="brand">
    <span class="brand__mark"></span>
    <span class="brand__name">Corvin Ridge<br>Software</span>
  </div>
</main>
</body>
</html>
```